business card for a massage therapy practice named 'Cedar and Willow Massage Studio'

I really need a trendy, yet easy on the eyes business card to complement my logo. Ideally with some gold or rose gold foil work.

My uploaded file of the logo I have in horizontal but I have a vertical version as well. Another color that is used in the website is a blush pink here and there. I'd like to see some trendy tropical leaves in the design.

```html
<!DOCTYPE html>
<html lang="en">
<head>
<meta charset="utf-8">
<title>Cedar and Willow Massage Studio – Business Card</title>
<link href="https://fonts.googleapis.com/css2?family=Montserrat:wght@400;500&family=Norican&display=swap" rel="stylesheet">
<style>
  :root {
    --backdrop: #4b4c4c;
    --card-black: #1c1c1c;
    --copper: #c88a52;
    --copper-deep: #8f5a2e;
    --copper-light: #e0a872;
  }
  * { margin: 0; padding: 0; box-sizing: border-box; }
  html, body {
    width: 1137px;
    height: 1200px;
    overflow: hidden;
    background: var(--backdrop);
  }
  .canvas {
    position: relative;
    width: 1137px;
    height: 1200px;
  }
  .card {
    position: absolute;
    left: 218px;
    width: 700px;
    height: 396px;
    background: var(--card-black);
    overflow: hidden;
  }
  .card--front { top: 180px; }
  .card--back { top: 668px; }

  /* Front */
  .brand {
    position: absolute;
    left: 0; right: 0;
    top: 150px;
    display: flex;
    align-items: center;
    justify-content: center;
    gap: 22px;
  }
  .brand__mark {
    width: 26px;
    height: 26px;
    border-radius: 50%;
    background: var(--copper);
    flex: none;
  }
  .brand__name {
    font-family: "Montserrat", sans-serif;
    font-weight: 500;
    color: var(--copper);
    text-transform: uppercase;
    letter-spacing: 0.14em;
    line-height: 1.35;
  }
  .brand__line { display: block; font-size: 34px; }
  .brand__line--sub { font-size: 22px; letter-spacing: 0.32em; }

  /* Back */
  .foliage {
    position: absolute;
  }
  .foliage--left {
    left: 0; top: 28px;
    width: 262px; height: 368px;
    background: linear-gradient(150deg, rgba(200,138,82,0.0) 0%, rgba(200,138,82,0.55) 55%, rgba(143,90,46,0.75) 100%);
    clip-path: polygon(95% 0, 100% 25%, 60% 70%, 15% 100%, 0 100%, 0 45%);
  }
  .foliage--right {
    right: 0; top: 12px;
    width: 176px; height: 250px;
    background: linear-gradient(200deg, rgba(224,168,114,0.7) 0%, rgba(200,138,82,0.45) 60%, rgba(200,138,82,0) 100%);
    clip-path: polygon(0 10%, 40% 0, 100% 20%, 100% 100%, 80% 75%, 40% 30%);
  }
  .contact {
    position: absolute;
    left: 262px;
    right: 40px;
    top: 158px;
    text-align: center;
    color: var(--copper);
  }
  .contact__name {
    font-family: "Norican", cursive;
    font-size: 38px;
    line-height: 1;
    margin-bottom: 22px;
  }
  .contact__list {
    list-style: none;
    font-family: "Montserrat", sans-serif;
    font-size: 15px;
    line-height: 24px;
  }
  .contact__list--address { margin-top: 12px; }
</style>
</head>
<body>
<main class="canvas">
  <section class="card card--front" aria-label="Card front">
    <div class="brand">
      <span class="brand__mark" aria-hidden="true"></span>
      <h1 class="brand__name">
        <span class="brand__line">Cedar and Willow</span>
        <span class="brand__line brand__line--sub">Massage Studio</span>
      </h1>
    </div>
  </section>

  <section class="card card--back" aria-label="Card back">
    <div class="foliage foliage--left" role="img" aria-label="Copper foil palm frond illustration"></div>
    <div class="foliage foliage--right" role="img" aria-label="Copper foil palm leaf illustration"></div>
    <div class="contact">
      <h2 class="contact__name">Marisol Vega</h2>
      <ul class="contact__list">
        <li>(555) 214-0387</li>
        <li>info@cedarandwillow.com</li>
        <li>www.cedarandwillow.com</li>
      </ul>
      <ul class="contact__list contact__list--address">
        <li>418 Linden Ave #12</li>
        <li>Riverton, CA 95021</li>
      </ul>
    </div>
  </section>
</main>
</body>
</html>
```